A website for a Maltese Law Firm

Our law firm needs a website to further its business. The site should have a simple yet effective design. We would need the following sections: About us, Practice Areas, About Malta, Contact. These should be further split as follows:

About us: Our firm, Our values, What others say, Offices

Practice Areas: Crimimal, Citizenship & Residence, Sovereign Patron Pathway, Criminal Defence, Civil Litigation, Arbitration and ADR, Commercial and Corporate, Media Law.

About Malta: just one section.

Contact: Just one section

We would also need a news feed at the front of the site to include latest news regarding our cases.

At the bottom we need a section for our Terms and a Privacy Statement.

Our logo is being attached.

Target Market(s)

All clients looking for legal assistance in Malta

Industry/Entity Type

Legal

Coding

Coded - Design and coding required

Number of Pages Required

1 page

Requirements
Must have
• It must be simple yet striking.

```html
<!DOCTYPE html>
<html lang="en">
<head>
<meta charset="utf-8">
<title>Zammit &amp; Farrugia Advocates</title>
<link rel="stylesheet" href="https://fonts.googleapis.com/css2?family=Cinzel:wght@400;600&family=Montserrat:wght@400;600&display=swap">
<style>
:root{
  --ink:#222;
  --text:#555;
  --muted:#777;
  --dark:#2f2f2f;
  --footer:#333;
  --line:#cfcfcf;
  --panel:#f0f0f0;
  --news:#e5eaf1;
  --white:#fff;
}
*{box-sizing:border-box;margin:0;padding:0}
html,body{width:1200px;height:2397px;overflow:hidden;background:var(--white)}
body{position:relative;font-family:'Montserrat',sans-serif;color:var(--text)}
.abs{position:absolute}
.serif{font-family:'Cinzel',serif}
/* top bar */
.topbar{left:0;top:0;width:1200px;height:35px;border-bottom:1px solid #e3e3e3}
.social{left:99px;top:0;height:35px;display:flex}
.social span{width:39px;height:35px;border-left:1px solid #e3e3e3;display:flex;align-items:center;justify-content:center}
.social span:last-child{border-right:1px solid #e3e3e3}
.social i{width:9px;height:9px;background:#666;border-radius:50%}
.callbar{left:880px;top:0;width:221px;height:35px;background:var(--dark);color:var(--white);font-size:11.5px;letter-spacing:.5px;display:flex;align-items:center;justify-content:center;gap:10px}
/* header */
.header{left:0;top:35px;width:1200px;height:77px;border-bottom:1px solid #ddd}
.logo{left:99px;top:20px;font-size:26px;color:var(--ink);letter-spacing:.5px;border-bottom:1px solid var(--ink);padding-bottom:4px}
.nav{top:30px;font-family:'Cinzel',serif;font-size:14px;color:var(--ink);letter-spacing:.3px}
.nav.active{border-top:1px solid var(--ink);border-bottom:2px solid var(--ink);padding:4px 3px}
.nav.active{top:26px}
/* hero */
.hero{left:0;top:112px;width:1200px;height:466px;background:linear-gradient(90deg,#8d98ae 0%,#b9bcc2 25%,#cfcfcf 50%,#b8b8b8 75%,#6e6e6e 100%)}
.hero-title{left:101px;top:300px;font-size:27px;line-height:34px;color:var(--ink);font-weight:600}
.hero-btn{left:99px;top:387px;border:1px solid var(--ink);padding:7px 10px;font-family:'Cinzel',serif;font-size:12px;color:var(--ink)}
.arrow{top:310px}
/* section titles */
.title{font-family:'Cinzel',serif;font-size:25px;color:#555;letter-spacing:.5px;white-space:nowrap}
.title b{font-weight:400;color:var(--ink);border-bottom:2px solid var(--ink);padding-bottom:1px}
.center{left:0;width:1200px;text-align:center}
/* about */
.about-text{left:99px;top:689px;width:592px;font-size:13.5px;line-height:25.5px;color:var(--text)}
.btn-dark{left:99px;top:857px;width:134px;height:38px;background:var(--dark);color:var(--white);font-family:'Cinzel',serif;font-size:13px;display:flex;align-items:center;justify-content:center}
.feature-icon{width:96px;height:94px;border:1px solid #ccc;display:flex;align-items:center;justify-content:center}
.feature-title{font-family:'Cinzel',serif;font-size:17px;color:var(--ink)}
.feature-text{width:240px;font-size:12px;line-height:19px;color:var(--muted)}
/* practice */
.practice{left:0;top:946px;width:1200px;height:350px;background:linear-gradient(180deg,#efefef,#f3f3f3 60%,#e9e9e9)}
.area{top:1063px;width:152px}
.area-box{height:97px;border:1px solid #ccc;background:#f6f6f6;display:flex;align-items:center;justify-content:center}
.area-label{height:52px;margin-top:6px;border-bottom:1px solid #999;font-family:'Cinzel',serif;font-size:13px;line-height:15px;color:var(--ink);text-align:center;display:flex;align-items:center;justify-content:center}
.dots{top:1241px;left:582px;display:flex;gap:4px}
.dots i{width:9px;height:9px;border:1px solid #888;border-radius:50%}
.dots i:first-child{background:radial-gradient(#555 35%,transparent 40%)}
/* malta */
.frame{left:99px;top:1401px;width:422px;height:245px;border:1px solid #ccc}
.malta-img{left:115px;top:1419px;width:422px;height:248px;background:linear-gradient(180deg,#4d79b8 0%,#7ea3d3 35%,#d6a35a 55%,#e6a54c 62%,#6f8fc8 75%,#4a6db8 100%)}
.malta-text{left:567px;top:1404px;width:534px;font-size:13.5px;line-height:25.5px}
.bullets{left:567px;top:1563px;width:534px;list-style:none}
.bullets li{position:relative;padding-left:24px;font-size:13px;line-height:17px;font-weight:600;color:var(--ink);margin-bottom:15px}
.bullets svg{position:absolute;left:0;top:3px}
/* news */
.news{left:0;top:1720px;width:1200px;height:455px;background:linear-gradient(90deg,#eef1f6,#e3e8f0 70%,#dfe5ee)}
.news-img{top:1833px;width:479px;height:172px}
.date{left:0;bottom:0;width:60px;height:60px;background:var(--dark);color:var(--white);text-align:center;font-size:12px;padding-top:6px}
.date b{display:block;font-size:20px;font-weight:600}
.news-text{top:2022px;width:479px;font-size:12.5px;line-height:25px}
.btn-line{top:2089px;height:35px;border:1px solid var(--ink);font-family:'Cinzel',serif;font-size:13px;color:var(--ink);display:flex;align-items:center;padding:0 17px}
/* footer */
.footer{left:0;top:2175px;width:1200px;height:222px;background:var(--footer);color:#ddd}
.f-logo{left:121px;top:2256px;font-size:24px;color:var(--white);border-bottom:1px solid #ccc;padding-bottom:3px}
.copy{left:99px;top:2312px;font-size:11.5px;color:#ccc}
.f-head{top:2221px;font-family:'Cinzel',serif;font-size:16px;letter-spacing:1px;color:var(--white);border-bottom:1px solid #888;padding-bottom:6px}
.f-link{font-size:11.5px;color:#ccc;display:flex;align-items:center;gap:9px}
.f-link::before{content:"";width:6px;height:6px;border:1px solid #ccc;transform:rotate(45deg)}
.f-social{left:593px;top:2344px;display:flex;gap:14px}
.f-social i{width:11px;height:11px;background:#ddd;border-radius:2px}
.input{left:802px;top:2266px;width:253px;height:35px;background:#4a4a4a;font-size:11.5px;font-style:italic;color:#bbb;padding:11px 16px}
.send{left:1055px;top:2266px;width:46px;height:35px;background:#ddd;display:flex;align-items:center;justify-content:center}
.f-info{font-size:11.5px;color:#ddd;display:flex;align-items:center;gap:8px}
</style>
</head>
<body>

<!-- top bar -->
<div class="abs topbar"></div>
<div class="abs social"><span><i></i></span><span><i></i></span><span><i></i></span><span><i></i></span></div>
<div class="abs callbar">
  <svg width="14" height="14" viewBox="0 0 24 24"><path d="M6.6 10.8a15 15 0 0 0 6.6 6.6l2.2-2.2c.3-.3.7-.4 1-.2 1.1.4 2.3.6 3.6.6.6 0 1 .4 1 1V20c0 .6-.4 1-1 1A17 17 0 0 1 3 4c0-.6.4-1 1-1h3.5c.6 0 1 .4 1 1 0 1.3.2 2.5.6 3.6.1.3 0 .7-.2 1z" fill="#fff"/></svg>
  <span>CALL US : (356) 2555 0198</span>
</div>

<!-- header -->
<div class="abs header">
  <div class="abs logo serif">Zammit &amp; Farrugia</div>
  <div class="abs nav active" style="left:545px">Home</div>
  <div class="abs nav" style="left:634px">About us</div>
  <div class="abs nav" style="left:741px">Practice Areas</div>
  <div class="abs nav" style="left:893px">About Malta</div>
  <div class="abs nav" style="left:1031px">Contact</div>
</div>

<!-- hero -->
<div class="abs hero" role="img" aria-label="Photo of two hands passing a passport in front of a flag"></div>
<svg class="abs arrow" style="left:27px" width="44" height="44" viewBox="0 0 44 44"><path d="M14 4H4v36h10" fill="none" stroke="#222" stroke-width="2"/><path d="M40 22H12M20 14l-8 8 8 8" fill="none" stroke="#222" stroke-width="2"/></svg>
<svg class="abs arrow" style="left:1128px" width="44" height="44" viewBox="0 0 44 44"><path d="M30 4h10v36H30" fill="none" stroke="#555" stroke-width="2"/><path d="M4 22h28M24 14l8 8-8 8" fill="none" stroke="#555" stroke-width="2"/></svg>
<div class="abs hero-title serif">The Greatest &amp; Stongest<br>Firm You Can Trust</div>
<div class="abs hero-btn">Request A Free Consultant</div>

<!-- about -->
<div class="abs title" style="left:99px;top:638px">About <b>Zammit &amp; Farrugia</b></div>
<p class="abs about-text">Lorem ipsum dolor sit amet, consectetuer adipiscing elit, sed diam nonummy nibh euismod tincidunt ut laoreet dolore magna aliquam erat volutpat. Ut wisi enim ad minim veniam, quis nostrud exerci tation ullamcorper suscipit lobortis nisl ut aliquip ex ea commodo consequat. Duis autem vel eum iriure dolor in hendrerit in vulputate velit esse molestie consequat, vel illum dolore eu feugiat nulla facilisis at vero eros et accumsan et iusto odio dignissim qui blandit praesent luptatum &nbsp;te feugait nulla facilisi.</p>
<div class="abs btn-dark">Read More</div>

<div class="abs feature-icon" style="left:748px;top:663px">
  <svg width="64" height="40" viewBox="0 0 64 40"><path d="M2 10l12-6 8 4 10-3 10 3 8-4 12 6-6 14-8 6-6 6-6-4-6 4-6-4-6-2-6-8z" fill="none" stroke="#222" stroke-width="3" stroke-linejoin="round"/><path d="M24 16l8-4 12 10" fill="none" stroke="#222" stroke-width="3"/></svg>
</div>
<div class="abs feature-title" style="left:863px;top:664px">Our Values</div>
<div class="abs feature-text" style="left:865px;top:693px">Artis nisl ut aliquip ex ea commodoll eros et accumsan o digniss qui nulla facilis...[+]</div>

<div class="abs feature-icon" style="left:748px;top:791px">
  <svg width="56" height="48" viewBox="0 0 56 48"><path d="M28 2L4 14h48z" fill="#222"/><rect x="6" y="16" width="44" height="4" fill="#222"/><rect x="10" y="22" width="6" height="16" fill="#222"/><rect x="20" y="22" width="6" height="16" fill="#222"/><rect x="30" y="22" width="6" height="16" fill="#222"/><rect x="40" y="22" width="6" height="16" fill="#222"/><rect x="4" y="40" width="48" height="5" fill="#222"/></svg>
</div>
<div class="abs feature-title" style="left:863px;top:792px">Our Firm</div>
<div class="abs feature-text" style="left:865px;top:821px">Artis nisl ut aliquip ex ea commodoll eros et accumsan o digniss qui nulla facilis...[+]</div>

<!-- practice areas -->
<div class="abs practice"></div>
<div class="abs title center" style="top:988px">Practice <b>Areas</b></div>

<div class="abs area" style="left:99px">
  <div class="area-box"><svg width="60" height="48" viewBox="0 0 60 48"><circle cx="16" cy="32" r="11" fill="none" stroke="#222" stroke-width="4"/><circle cx="44" cy="26" r="11" fill="none" stroke="#222" stroke-width="4"/><path d="M14 12l6-6 6 6M38 6l6-4 6 6" fill="none" stroke="#222" stroke-width="4"/><path d="M22 20q8-8 16 0" fill="none" stroke="#222" stroke-width="3"/></svg></div>
  <div class="area-label">Criminal Law</div>
</div>
<div class="abs area" style="left:312px">
  <div class="area-box"><svg width="52" height="46" viewBox="0 0 52 46"><path d="M26 2L2 24h7v20h13V32h8v12h13V24h7z" fill="#222"/></svg></div>
  <div class="area-label">Citizenship &amp;<br>Residence</div>
</div>
<div class="abs area" style="left:524px">
  <div class="area-box"><svg width="52" height="50" viewBox="0 0 52 50"><circle cx="24" cy="16" r="12" fill="#222"/><path d="M4 48q2-18 20-18t20 18z" fill="#222"/><path d="M34 30l12 12-4 1 3 5-3 1-3-5-3 3z" fill="#222" stroke="#f6f6f6" stroke-width="1.5"/></svg></div>
  <div class="area-label">Sovereign Patron<br>Pathway</div>
</div>
<div class="abs area" style="left:737px">
  <div class="area-box"><svg width="52" height="48" viewBox="0 0 52 48"><rect x="18" y="2" width="14" height="22" rx="2" transform="rotate(-45 25 13)" fill="#222"/><path d="M28 22l16 16" stroke="#222" stroke-width="5" stroke-linecap="round"/><rect x="4" y="40" width="26" height="6" fill="#222"/></svg></div>
  <div class="area-label">Civil<br>Litigation</div>
</div>
<div class="abs area" style="left:949px">
  <div class="area-box"><svg width="52" height="48" viewBox="0 0 52 48"><rect x="10" y="2" width="32" height="30" fill="#222"/><circle cx="26" cy="13" r="5" fill="#f6f6f6"/><rect x="18" y="20" width="16" height="8" rx="3" fill="#f6f6f6"/><rect x="4" y="35" width="44" height="4" fill="#222"/><rect x="2" y="42" width="48" height="4" fill="#222"/></svg></div>
  <div class="area-label">Arbitration<br>and ADR</div>
</div>
<div class="abs dots"><i></i><i></i><i></i></div>

<!-- about malta -->
<div class="abs title center" style="top:1341px">About <b>Malta</b></div>
<div class="abs frame"></div>
<div class="abs malta-img" role="img" aria-label="Photo of the Valletta skyline lit at dusk over the harbour"></div>
<p class="abs malta-text">Aeuismod tincidunt ut laoreet dolore magna aliquam erat volutpat. Ut wisi enim ad minim veniam, quis nostrud exerci tation ullamcorper suscipit lobortis nisl ut aliquip ex ea commodo consequat. Duis autem vel eum iriure dolor in hendrerit in vulputate velit esse molestie consequat, vel illum dolore eu feugiat nulla facilisis at vero eros et accumsan et iusto odio dignissim qui blandit praesent luptatum &nbsp;te feugait nulla facilisi.</p>
<ul class="abs bullets">
  <li><svg width="12" height="12" viewBox="0 0 12 12"><path d="M1 6h9M6 2l4 4-4 4" fill="none" stroke="#222" stroke-width="1.5"/></svg>Duis autem vel eum iriure dolor in hendrerit in vulputate vl conseqt,molestie consequat vel illum dolore.</li>
  <li><svg width="12" height="12" viewBox="0 0 12 12"><path d="M1 6h9M6 2l4 4-4 4" fill="none" stroke="#222" stroke-width="1.5"/></svg>Ut wisi enim ad minim veniam, qui nostrud exeullamcorper suscipit lobortis .</li>
  <li><svg width="12" height="12" viewBox="0 0 12 12"><path d="M1 6h9M6 2l4 4-4 4" fill="none" stroke="#222" stroke-width="1.5"/></svg>Aulputate velit esse molestie consequat, vel illum dolore eu feugiat.</li>
</ul>

<!-- latest news -->
<div class="abs news"></div>
<div class="abs title center" style="top:1758px">Latest <b>News</b></div>

<div class="abs news-img" style="left:99px;background:linear-gradient(135deg,#1d242c,#3e4a55 50%,#1a1f24)" role="img" aria-label="Photo of a lawyer reading documents at a desk">
  <div class="abs date"><b>08</b>JUNE</div>
</div>
<p class="abs news-text" style="left:99px">lobortis nisl ut aliquip ex ea commodo consequat. Duis autem vel eum iriure dolor in hendrerit inilore eu feugiat nulla facilisis at vero..</p>
<div class="abs btn-line" style="left:99px">Read More</div>

<div class="abs news-img" style="left:622px;background:linear-gradient(135deg,#e8e2d6,#c8a678 45%,#6e3e1e 75%,#f2efe9)" role="img" aria-label="Photo of a wooden gavel resting on an open law book">
  <div class="abs date"><b>08</b>JUNE</div>
</div>
<p class="abs news-text" style="left:622px">lobortis nisl ut aliquip ex ea commodo consequat. Duis autem vel eum iriure dolor in hendrerit in vulpue molestie ct, velo..</p>
<div class="abs btn-line" style="left:622px">Read More</div>

<!-- footer -->
<div class="abs footer"></div>
<div class="abs f-logo serif">Zammit &amp; Farrugia</div>
<div class="abs copy">Copyright © 2016 ZFadvocates. All rights reserved.</div>

<div class="abs f-head" style="left:465px">Navigation</div>
<div class="abs f-link" style="left:460px;top:2265px">Home</div>
<div class="abs f-link" style="left:588px;top:2265px">About Malta</div>
<div class="abs f-link" style="left:460px;top:2304px">About us</div>
<div class="abs f-link" style="left:588px;top:2304px">Contact Us</div>
<div class="abs f-link" style="left:460px;top:2344px">Practice Areas</div>
<div class="abs f-social"><i></i><i></i><i></i><i></i></div>

<div class="abs f-head" style="left:799px">Newsletter</div>
<div class="abs input">Enter Your Email</div>
<div class="abs send"><svg width="20" height="18" viewBox="0 0 20 18"><path d="M1 8L19 1l-4 16-5-5-3 4v-6l8-6-9 5z" fill="none" stroke="#333" stroke-width="1.4" stroke-linejoin="round"/></svg></div>
<div class="abs f-info" style="left:808px;top:2318px"><svg width="10" height="13" viewBox="0 0 10 13"><path d="M5 0a5 5 0 0 1 5 5c0 3-5 8-5 8S0 8 0 5a5 5 0 0 1 5-5z" fill="#ddd"/><circle cx="5" cy="5" r="2" fill="#333"/></svg>58 Lantern Street, Mosta</div>
<div class="abs f-info" style="left:808px;top:2347px"><svg width="12" height="12" viewBox="0 0 24 24"><path d="M6.6 10.8a15 15 0 0 0 6.6 6.6l2.2-2.2c.3-.3.7-.4 1-.2 1.1.4 2.3.6 3.6.6.6 0 1 .4 1 1V20c0 .6-.4 1-1 1A17 17 0 0 1 3 4c0-.6.4-1 1-1h3.5c.6 0 1 .4 1 1 0 1.3.2 2.5.6 3.6.1.3 0 .7-.2 1z" fill="#ddd"/></svg>(356) 2555 0198</div>
<div class="abs f-info" style="left:944px;top:2347px"><svg width="14" height="10" viewBox="0 0 14 10"><rect width="14" height="10" fill="#ddd"/><path d="M0 0l7 6 7-6" fill="none" stroke="#333" stroke-width="1.2"/></svg>info@zfadvocates.com</div>

</body>
</html>
```